Banner dimension 1767 X 887 for Tovrelli website

Need one banner for our website www.tovrelli.com.au, The dimension of the banner should be 1767 x 887. Attached to this brief are two images that needs to be on that one banner, PLEASE DO NOT SEND SEPARATE BANNERS, both images on the same banner. Thanks

The banner should have the following message on it:

1.) " Take a further 40% off all stock" ( use code: TOVRELLI. Ends 31/12/2015)
2.) " Kick back or kick it up a notch this Autumn in the most versatile pique striped polo shirts and Pinafore belt strap denim dress"

Target Market(s)

kids aged 5-12yrs

Requirements
Must have
• very playful

```html
<!DOCTYPE html>
<html lang="en">
<head>
<meta charset="utf-8">
<title>Tovrelli – Further 40% Off All Stock</title>
<link rel="stylesheet" href="https://fonts.googleapis.com/css2?family=Big+Shoulders+Stencil+Display:wght@700;900&family=Black+Ops+One&family=Oswald:wght@400&display=swap">
<style>
  :root {
    --teal: #1c7ea3;
    --magenta: #e2187f;
    --ink: #111111;
    --strip: #2b2b2d;
    --strip-text: #f4f4f4;
    --panel: rgba(255, 255, 255, 0.72);
    --wash-lilac: #c9c3e3;
    --wash-blue: #a9cfe0;
    --wash-mint: #bfe3d8;
    --wash-pale: #eeeef4;
  }
  * { box-sizing: border-box; margin: 0; padding: 0; }
  html, body { width: 1200px; height: 602px; overflow: hidden; background: #fff; }

  .banner { position: relative; width: 1200px; height: 602px; overflow: hidden; }
  .watercolour-wash {
    position: absolute; inset: 0;
    background:
      radial-gradient(ellipse 420px 300px at 120px 180px, var(--wash-blue), transparent 70%),
      radial-gradient(ellipse 380px 260px at 260px 480px, var(--wash-lilac), transparent 70%),
      radial-gradient(ellipse 420px 300px at 1050px 150px, var(--wash-mint), transparent 70%),
      radial-gradient(ellipse 400px 300px at 950px 470px, var(--wash-lilac), transparent 70%),
      radial-gradient(ellipse 300px 220px at 640px 560px, var(--wash-blue), transparent 70%),
      var(--wash-pale);
  }
  .offer-panel {
    position: absolute; left: 340px; top: 0;
    width: 433px; height: 440px;
    background: var(--panel);
  }
  .model-photo { position: absolute; border-radius: 40px; opacity: 0.55; }
  .model-photo--girl {
    left: 62px; top: 22px; width: 270px; height: 555px;
    background: linear-gradient(180deg, #6b4a3a 0%, #f2f2f2 20%, #4d77a0 40%, #5f88ad 62%, #d9b9a4 80%, #e8709a 100%);
  }
  .model-photo--boy {
    left: 778px; top: 55px; width: 345px; height: 490px;
    background: linear-gradient(180deg, #5a3a2a 0%, #d9b39b 18%, #3f7a5a 32%, #243028 48%, #8eaac4 66%, #d9b9a4 82%, #2a2a2a 100%);
  }

  .offer-line {
    position: absolute;
    white-space: nowrap;
    line-height: 1;
    transform-origin: left top;
  }
  .offer-line--further {
    left: 410px; top: 52px;
    font-family: "Big Shoulders Stencil Display", sans-serif;
    font-weight: 700;
    font-size: 58px;
    letter-spacing: 1.5px;
    color: var(--teal);
  }
  .offer-line--figure {
    left: 406px; top: 100px;
    font-family: "Black Ops One", sans-serif;
    font-size: 172px;
    letter-spacing: -4px;
    color: var(--magenta);
  }
  .offer-line--percent {
    left: 670px; top: 112px;
    font-family: "Big Shoulders Stencil Display", sans-serif;
    font-weight: 900;
    font-size: 88px;
    color: var(--magenta);
  }
  .offer-line--off {
    left: 671px; top: 184px;
    font-family: "Big Shoulders Stencil Display", sans-serif;
    font-weight: 900;
    font-size: 76px;
    color: var(--magenta);
    transform: scaleX(0.62);
  }
  .offer-line--stock {
    left: 410px; top: 254px;
    font-family: "Black Ops One", sans-serif;
    font-size: 60px;
    color: var(--teal);
    transform: scaleX(0.88);
  }
  .offer-line--code {
    left: 407px; top: 314px;
    font-family: "Oswald", sans-serif;
    font-size: 38px;
    letter-spacing: 1px;
    color: var(--magenta);
  }
  .offer-line--code strong { font-weight: 400; }
  .offer-line--ends {
    left: 407px; top: 346px;
    font-family: "Oswald", sans-serif;
    font-size: 60px;
    color: var(--ink);
    transform: scaleX(0.84);
  }

  .tagline-strip {
    position: absolute;
    background: var(--strip);
    color: var(--strip-text);
    font-family: "Oswald", sans-serif;
    text-transform: uppercase;
    white-space: nowrap;
    padding: 0 18px;
  }
  .tagline-strip--lead {
    left: 294px; top: 424px; height: 40px;
    font-size: 27px; line-height: 40px; letter-spacing: 3px;
    transform: rotate(-1deg);
  }
  .tagline-strip--mid {
    left: 372px; top: 486px; height: 32px;
    font-size: 19px; line-height: 32px; letter-spacing: 2.4px;
    transform: rotate(-1deg);
  }
  .tagline-strip--last {
    left: 290px; top: 524px; height: 34px;
    font-size: 19px; line-height: 34px; letter-spacing: 3px;
    transform: rotate(-0.8deg);
  }
</style>
</head>
<body>
<main class="banner">
  <div class="watercolour-wash" role="img" aria-label="Soft pastel watercolour texture in blue, lilac and mint"></div>

  <div class="model-photo model-photo--girl" role="img" aria-label="Smiling girl in a white tee, denim pinafore dress and pink sneakers"></div>
  <div class="offer-panel"></div>
  <div class="model-photo model-photo--boy" role="img" aria-label="Playful boy in a green striped pique polo, denim cargo shorts and black sneakers"></div>

  <p class="offer-line offer-line--further">TAKE A FURTHER</p>
  <p class="offer-line offer-line--figure">40</p>
  <p class="offer-line offer-line--percent">%</p>
  <p class="offer-line offer-line--off">OFF</p>
  <p class="offer-line offer-line--stock">ALL STOCK</p>
  <p class="offer-line offer-line--code">use code: <strong>TOVRELLI</strong></p>
  <p class="offer-line offer-line--ends">ends 31/12/2015</p>

  <p class="tagline-strip tagline-strip--lead">Kick back or kick it up a notch</p>
  <p class="tagline-strip tagline-strip--mid">This autumn in the most versatile pique striped</p>
  <p class="tagline-strip tagline-strip--last">Polo shirts and pinafore belt strap denim dress</p>
</main>
</body>
</html>
```